Graphic design for "How It Works" for VelmoraAttire.net*

VelmoraAttire.net website is for selling custom designer outfits for women and girls in all countries, customers can choose existing designs on this website and customize to their measurements. Customers can also provide their own designs and measurements and our expert designers and tailors get the outfit stitched and delivered to the customer.

We wanted to explain how this entire process works in 4 steps in the form of graphic design with little heading and text describing each step.

Step 1: Select Dress
Its time to choose the beauty you want to adorn yourself with. We have a wide collection of premium dresses, colours and accessories. There is something for everyone! All you need to do is pick. If you can’t find what you are looking for then you can share a picture of what you want, we will get it done whatever you want.

Step 2: Customization
Everyone is different; hence we realise the need for customization of the design and size. Here you select exactly how you want your dress to be. From sleeves to cuts, everything will be done as per your wish. Enter your measurements, lo and behold! You’re done. Leave your comments for even more customization.

Step 3: Designer Consultation
We as a user-friendly brand, aspire to provide the best of services to our clients. Our expert lady designers will help you for everything right from selecting of fabric to design of dress to necessary accessories. Our designers are just a call away!

Step 4: Stitch and Deliver
After you have placed your order, we confirm and verify the details. The boutique completes your order, sends it to us and we deliver it to your doorstep. We also have a team of designers in-house to cater to your premium dressing needs.

```html
<!DOCTYPE html>
<html lang="en">
<head>
<meta charset="utf-8">
<title>How It Works – VelmoraAttire.net</title>
<link rel="stylesheet" href="https://fonts.googleapis.com/css2?family=Montserrat:wght@300;400&display=swap">
<style>
  :root {
    --board: #5a5a5a;
    --paper: #ffffff;
    --ink: #555a60;
    --rose: #ea5c9d;
    --ring: #f4a5b9;
    --ring-soft: #fbd0c2;
    --slate: #404850;
    --berry: #c85386;
    --on-fill: #ffffff;
  }
  * { box-sizing: border-box; margin: 0; padding: 0; }
  html, body { width: 1083px; height: 1200px; overflow: hidden; background: var(--board); }
  body { position: relative; font-family: "Montserrat", Arial, sans-serif; font-weight: 300; color: var(--ink); }

  .variant { position: absolute; left: 15.5px; width: 1052px; height: 378px; background: var(--paper); overflow: hidden; }
  .variant--outline { top: 18px; }
  .variant--slate { top: 414px; }
  .variant--berry { top: 806px; }

  .section-badge { position: absolute; left: 452px; top: -78px; width: 148px; height: 148px; border-radius: 50%;
    border: 2px solid var(--ring-soft); border-top-color: var(--ring); border-left-color: var(--ring); }
  .section-title { position: absolute; left: 0; width: 100%; top: 19px; text-align: center; font-size: 13.2px;
    letter-spacing: 0.6px; font-weight: 400; color: var(--ink); }

  .step { position: absolute; top: 120px; width: 235px; height: 240px; border-radius: 6px; text-align: center;
    padding-top: 38px; }
  .step:nth-of-type(1) { left: 47px; }
  .step:nth-of-type(2) { left: 288.5px; }
  .step:nth-of-type(3) { left: 530px; }
  .step:nth-of-type(4) { left: 771px; }

  .step__photo { position: absolute; left: 67px; top: -73px; width: 101px; height: 101px; border-radius: 50%;
    border: 2.4px solid var(--ring); }
  .photo--wardrobe { background: radial-gradient(circle at 62% 38%, #e8cbb4 0 18%, #d9cfc6 38%, #b8aea6 70%, #efe8e2); }
  .photo--fitting { background: linear-gradient(110deg, #f2ece4 0 35%, #d8c7b6 50%, #2c2a2c 70%, #e9e2d8 90%); }
  .photo--consult { background: radial-gradient(circle at 48% 35%, #e6c2a6 0 15%, #b9c6d6 45%, #eae5df 80%); }
  .photo--sewing { background: radial-gradient(circle at 35% 40%, #f7b48f 0 25%, #f3d6c6 55%, #c9c2bd 90%); }

  .step__label, .step__name { display: block; font-size: 14.3px; line-height: 16.5px; }
  .step__text { margin-top: 12px; font-size: 10.2px; line-height: 12.85px; }

  .variant--outline .step { border: 1.2px solid #f7bfc9; background: var(--paper); }
  .variant--outline .step__label, .variant--outline .step__name { color: var(--rose); }

  .variant--slate .step { background: var(--slate); color: var(--on-fill); }
  .variant--slate .step__photo { border: 2.4px solid var(--paper); }

  .variant--berry .step { background: var(--berry); color: var(--on-fill); }
  .variant--berry .step__name { font-size: 18.5px; line-height: 21px; margin-top: 1px; }
  .variant--berry .step__text { margin-top: 3px; }
</style>
</head>
<body>

<section class="variant variant--outline">
  <div class="section-badge"></div>
  <h2 class="section-title">HOW IT WORKS</h2>
  <article class="step">
    <div class="step__photo photo--wardrobe" role="img" aria-label="Photo of a smiling woman holding an armful of clothes"></div>
    <h3><span class="step__label">Step 1:</span><span class="step__name">Select Dress</span></h3>
    <p class="step__text">Its time to choose<br>the beauty you want to adorn<br>yourself with. We have a wide<br>collection of premium dresses, colours<br>and accessories. There is something<br>for everyone! All you need<br>to do is pick. If you can’t find<br>what you are looking for then<br>you can share a picture of what<br>you want, we will get it done<br>whatever you want.</p>
  </article>
  <article class="step">
    <div class="step__photo photo--fitting" role="img" aria-label="Photo of a designer fitting fabric on a dress form"></div>
    <h3><span class="step__label">Step 2:</span><span class="step__name">Customization</span></h3>
    <p class="step__text">Everyone is different;<br>hence we realise the need for<br>customization of the design and size.<br>Here you select exactly how<br>you want your dress to be.<br>From sleeves to cuts, everything<br>will be done as per your wish.<br>Enter your measurements,<br>lo and behold! You’re done.<br>Leave your comments for even<br>more customization.</p>
  </article>
  <article class="step">
    <div class="step__photo photo--consult" role="img" aria-label="Photo of a designer talking on the phone in her studio"></div>
    <h3><span class="step__label">Step 3:</span><span class="step__name">Designer Consultation</span></h3>
    <p class="step__text">We as a user-friendly brand,<br>aspire to provide the best<br>of services to our clients.<br>Our expert<br>lady designers will help you<br>for everything right from<br>selecting of fabric<br>to design of dress<br>to necessary accessories.<br>Our designers are<br>just a call away!</p>
  </article>
  <article class="step">
    <div class="step__photo photo--sewing" role="img" aria-label="Photo of hands guiding fabric through a sewing machine"></div>
    <h3><span class="step__label">Step 4:</span><span class="step__name">Stitch and Deliver</span></h3>
    <p class="step__text">After you have placed<br>your order, we confirm<br>and verify the details.<br>The boutique completes<br>your order,<br>sends it to us and we deliver it<br>to your doorstep.<br>We also have a team of<br>designers in-house<br>to cater to your<br>premium dressing needs.</p>
  </article>
</section>

<section class="variant variant--slate">
  <div class="section-badge"></div>
  <h2 class="section-title">HOW IT WORKS</h2>
  <article class="step">
    <div class="step__photo photo--wardrobe" role="img" aria-label="Photo of a smiling woman holding an armful of clothes"></div>
    <h3><span class="step__label">Step 1:</span><span class="step__name">Select Dress</span></h3>
    <p class="step__text">Its time to choose<br>the beauty you want to adorn<br>yourself with. We have a wide<br>collection of premium dresses, colours<br>and accessories. There is something<br>for everyone! All you need<br>to do is pick. If you can’t find<br>what you are looking for then<br>you can share a picture of what<br>you want, we will get it done<br>whatever you want.</p>
  </article>
  <article class="step">
    <div class="step__photo photo--fitting" role="img" aria-label="Photo of a designer fitting fabric on a dress form"></div>
    <h3><span class="step__label">Step 2:</span><span class="step__name">Customization</span></h3>
    <p class="step__text">Everyone is different;<br>hence we realise the need for<br>customization of the design and size.<br>Here you select exactly how<br>you want your dress to be.<br>From sleeves to cuts, everything<br>will be done as per your wish.<br>Enter your measurements,<br>lo and behold! You’re done.<br>Leave your comments for even<br>more customization.</p>
  </article>
  <article class="step">
    <div class="step__photo photo--consult" role="img" aria-label="Photo of a designer talking on the phone in her studio"></div>
    <h3><span class="step__label">Step 3:</span><span class="step__name">Designer Consultation</span></h3>
    <p class="step__text">We as a user-friendly brand,<br>aspire to provide the best<br>of services to our clients.<br>Our expert<br>lady designers will help you<br>for everything right from<br>selecting of fabric<br>to design of dress<br>to necessary accessories.<br>Our designers are<br>just a call away!</p>
  </article>
  <article class="step">
    <div class="step__photo photo--sewing" role="img" aria-label="Photo of hands guiding fabric through a sewing machine"></div>
    <h3><span class="step__label">Step 4:</span><span class="step__name">Stitch and Deliver</span></h3>
    <p class="step__text">After you have placed<br>your order, we confirm<br>and verify the details.<br>The boutique completes<br>your order,<br>sends it to us and we deliver it<br>to your doorstep.<br>We also have a team of<br>designers in-house<br>to cater to your<br>premium dressing needs.</p>
  </article>
</section>

<section class="variant variant--berry">
  <div class="section-badge"></div>
  <h2 class="section-title">HOW IT WORKS</h2>
  <article class="step">
    <div class="step__photo photo--wardrobe" role="img" aria-label="Photo of a smiling woman holding an armful of clothes"></div>
    <h3><span class="step__label">Step 1:</span><span class="step__name">Select Dress</span></h3>
    <p class="step__text">Its time to choose<br>the beauty you want to adorn<br>yourself with. We have a wide<br>collection of premium dresses, colours<br>and accessories. There is something<br>for everyone! All you need<br>to do is pick. If you can’t find<br>what you are looking for then<br>you can share a picture of what<br>you want, we will get it done<br>whatever you want.</p>
  </article>
  <article class="step">
    <div class="step__photo photo--fitting" role="img" aria-label="Photo of a designer fitting fabric on a dress form"></div>
    <h3><span class="step__label">Step 2:</span><span class="step__name">Customization</span></h3>
    <p class="step__text">Everyone is different;<br>hence we realise the need for<br>customization of the design and size.<br>Here you select exactly how<br>you want your dress to be.<br>From sleeves to cuts, everything<br>will be done as per your wish.<br>Enter your measurements,<br>lo and behold! You’re done.<br>Leave your comments for even<br>more customization.</p>
  </article>
  <article class="step">
    <div class="step__photo photo--consult" role="img" aria-label="Photo of a designer talking on the phone in her studio"></div>
    <h3><span class="step__label">Step 3:</span><span class="step__name">Designer Consultation</span></h3>
    <p class="step__text">We as a user-friendly brand,<br>aspire to provide the best<br>of services to our clients.<br>Our expert<br>lady designers will help you<br>for everything right from<br>selecting of fabric<br>to design of dress<br>to necessary accessories.<br>Our designers are<br>just a call away!</p>
  </article>
  <article class="step">
    <div class="step__photo photo--sewing" role="img" aria-label="Photo of hands guiding fabric through a sewing machine"></div>
    <h3><span class="step__label">Step 4:</span><span class="step__name">Stitch and Deliver</span></h3>
    <p class="step__text">After you have placed<br>your order, we confirm<br>and verify the details.<br>The boutique completes<br>your order,<br>sends it to us and we deliver it<br>to your doorstep.<br>We also have a team of<br>designers in-house<br>to cater to your<br>premium dressing needs.</p>
  </article>
</section>

</body>
</html>
```